Dusty Spur Outfitters Home Page

I need a logo and page design for my home page, maybe some background color suggestions to go with it. I want the logo to project "vintage" and "western wear" but not be your typical trite western saddle and gun type thing.
http://www.dustyspuroutfitters.example/store/cart.php
Not looking for page coding just logo and other design elements to lay in over the site's template to make it "pop"
Reason: Have to finalize the design.
Target Market(s)
My customers are 70/30 men to women.
Industry/Entity Type
Gun

```html
<!DOCTYPE html>
<html lang="en">
<head>
<meta charset="UTF-8">
<title>Dusty Spur Outfitters – Header Colour Options</title>
<link href="https://fonts.googleapis.com/css2?family=Lato:wght@700;900&family=Yesteryear&display=swap" rel="stylesheet">
<style>
  :root {
    --canvas: #d8c8a8;
    --canvas-deep: #cfbd9b;
    --teal: #3a9aab;
    --teal-dark: #2f8596;
    --band: #262626;
    --cream: #e8dcc2;
    --tagline: #e6d9bd;
    --ink: #2a2a2a;
    --gold: #f2c35a;
    --accent-red: #d8402a;
    --accent-teal: #6fb3c2;
    --accent-blue: #4aa3b8;
    --accent-gold: #f2c35a;
  }
  * { box-sizing: border-box; }
  html, body {
    margin: 0;
    width: 1200px;
    height: 1000px;
    overflow: hidden;
  }
  body {
    position: relative;
    background: linear-gradient(180deg, var(--canvas) 0%, var(--canvas-deep) 100%);
    font-family: "Lato", Arial, sans-serif;
  }
  .art-defs { position: absolute; width: 0; height: 0; }
  .header-option {
    position: absolute;
    left: 0;
    width: 1200px;
    height: 166px;
    box-shadow: 0 3px 4px rgba(60, 45, 25, 0.35);
  }
  .header-option--1 { top: 84px;  --dot: var(--accent-red); }
  .header-option--2 { top: 299px; --dot: var(--accent-teal); }
  .header-option--3 { top: 534px; --dot: var(--accent-blue); }
  .header-option--4 { top: 764px; --dot: var(--accent-gold); }

  .header-art {
    position: absolute;
    inset: 0;
    width: 1200px;
    height: 166px;
    display: block;
  }
  .brand {
    position: absolute;
    left: 62px;
    top: 2px;
    width: 406px;
    height: 158px;
    display: flex;
    align-items: center;
    justify-content: center;
    gap: 12px;
  }
  .brand-dot {
    width: 22px;
    height: 22px;
    border-radius: 50%;
    background: var(--dot);
    flex: none;
  }
  .brand-name {
    font-weight: 900;
    font-size: 33px;
    color: var(--gold);
    white-space: nowrap;
  }
  .tagline {
    position: absolute;
    left: 476px;
    top: 84px;
    margin: 0;
    font-family: "Yesteryear", cursive;
    font-size: 27px;
    letter-spacing: 0.6px;
    word-spacing: 3px;
    color: var(--tagline);
    white-space: nowrap;
  }
  .search {
    position: absolute;
    left: 901px;
    top: 52px;
    display: flex;
    align-items: center;
    gap: 11px;
  }
  .search-field {
    width: 173px;
    height: 29px;
    border-radius: 15px;
    background: var(--cream);
    color: var(--ink);
    font-weight: 700;
    font-size: 17px;
    line-height: 29px;
    padding-left: 17px;
  }
  .search-go {
    color: var(--cream);
    font-weight: 700;
    font-size: 18px;
  }
</style>
</head>
<body>

<svg class="art-defs" aria-hidden="true">
  <defs>
    <filter id="grunge" x="0" y="0" width="100%" height="100%">
      <feTurbulence type="fractalNoise" baseFrequency="0.018 0.07" numOctaves="4" seed="7" result="noise"/>
      <feColorMatrix in="noise" type="matrix"
        values="0 0 0 0 0.36
                0 0 0 0 0.36
                0 0 0 0 0.36
                0 0 0 2.6 -1.25" result="mottle"/>
      <feTurbulence type="fractalNoise" baseFrequency="0.9" numOctaves="1" seed="3" result="grain"/>
      <feColorMatrix in="grain" type="matrix"
        values="0 0 0 0 0.85
                0 0 0 0 0.82
                0 0 0 0 0.75
                0 0 0 9 -7.6" result="specks"/>
      <feMerge result="marks"><feMergeNode in="mottle"/><feMergeNode in="specks"/></feMerge>
      <feComposite in="marks" in2="SourceGraphic" operator="in" result="clipped"/>
      <feMerge><feMergeNode in="SourceGraphic"/><feMergeNode in="clipped"/></feMerge>
    </filter>
    <filter id="paper" x="0" y="0" width="100%" height="100%">
      <feTurbulence type="fractalNoise" baseFrequency="0.6" numOctaves="2" seed="11" result="n"/>
      <feColorMatrix in="n" type="matrix"
        values="0 0 0 0 0.1
                0 0 0 0 0.3
                0 0 0 0 0.35
                0 0 0 0.5 -0.1" result="tone"/>
      <feComposite in="tone" in2="SourceGraphic" operator="in" result="c"/>
      <feMerge><feMergeNode in="SourceGraphic"/><feMergeNode in="c"/></feMerge>
    </filter>
    <symbol id="header-backdrop" viewBox="0 0 1200 166">
      <rect width="1200" height="166" fill="#3a9aab" filter="url(#paper)"/>
      <path fill="#262626" filter="url(#grunge)" d="
        M0,22 L30,19 L58,24 L90,18 L120,21 L160,17 L200,23 L240,20 L275,25 L310,19 L350,22
        L400,18 L440,24 L480,20 L520,23 L560,17 L600,22 L650,19 L700,25 L740,20 L790,23
        L830,18 L880,24 L920,19 L960,22 L1000,26 L1040,20 L1080,23 L1120,18 L1160,24 L1200,21
        L1200,146 L1170,150 L1130,145 L1090,149 L1050,144 L1010,150 L970,146 L930,151
        L890,145 L850,149 L810,144 L770,150 L730,146 L690,148 L650,143 L610,150 L570,146
        L530,149 L490,144 L450,150 L410,145 L370,148 L330,143 L290,150 L250,146 L210,149
        L170,144 L130,150 L90,145 L50,149 L20,144 L0,148 Z"/>
      <path fill="none" stroke="#262626" stroke-width="2" opacity="0.8"
        d="M60,15 L140,14 M330,16 L420,15 M700,16 L760,15 M1050,17 L1150,15
           M100,154 L190,155 M520,153 L600,155 M880,154 L990,155"/>
    </symbol>
  </defs>
</svg>

<section class="header-option header-option--1">
  <svg class="header-art" aria-hidden="true"><use href="#header-backdrop" width="1200" height="166"/></svg>
  <div class="brand"><span class="brand-dot"></span><span class="brand-name">Dusty Spur Outfitters</span></div>
  <p class="tagline">Brand-New Retro Styled Western Wear</p>
  <div class="search"><div class="search-field">Search...</div><span class="search-go">GO!</span></div>
</section>

<section class="header-option header-option--2">
  <svg class="header-art" aria-hidden="true"><use href="#header-backdrop" width="1200" height="166"/></svg>
  <div class="brand"><span class="brand-dot"></span><span class="brand-name">Dusty Spur Outfitters</span></div>
  <p class="tagline">Brand-New Retro Styled Western Wear</p>
  <div class="search"><div class="search-field">Search...</div><span class="search-go">GO!</span></div>
</section>

<section class="header-option header-option--3">
  <svg class="header-art" aria-hidden="true"><use href="#header-backdrop" width="1200" height="166"/></svg>
  <div class="brand"><span class="brand-dot"></span><span class="brand-name">Dusty Spur Outfitters</span></div>
  <p class="tagline">Brand-New Retro Styled Western Wear</p>
  <div class="search"><div class="search-field">Search...</div><span class="search-go">GO!</span></div>
</section>

<section class="header-option header-option--4">
  <svg class="header-art" aria-hidden="true"><use href="#header-backdrop" width="1200" height="166"/></svg>
  <div class="brand"><span class="brand-dot"></span><span class="brand-name">Dusty Spur Outfitters</span></div>
  <p class="tagline">Brand-New Retro Styled Western Wear</p>
  <div class="search"><div class="search-field">Search...</div><span class="search-go">GO!</span></div>
</section>

</body>
</html>
```